Web Design Project

i'm looking for a sleek modern design i can use for a web site that deals with.
Intelligent Data Capture
Accounts Payable Solutions for faster processing based on our scanning solution.
ultimately we are a intelligent scanning software.

here is a great website, that does exactly what we do, and we like to have most of their services and products.

so something in this idea would be great.
www.valtrino.com

so i guess i want a good landing/home page which is smartly designed so users will be inclined to leave their information.

and then information pages.

also i dont need any cms for you to include, i only need you to hook the html hooks for RANK Kettle as i already have a CMS and need it to hook in to that, i am including links to that cheat sheet.
so it is easier when included as you create the Theme.

http://www.rankkettle.com/how-to-create-website-template.html
http://www.rankkettle.com/cheat-sheet.html
Updates

Hi Guys sorry for the long pause in design, but here is where we stand.

what ever design i choose, i need that designer to customize a few things for me based on design that was designed.
and i will need designer to match that them to work with RANK Kettle
here is the cheat sheet for the hooks that we need to match and make it work.
if you have any questions let me know.

otherwise i look forward to working with you. and good luck.

Target Market(s)

CFO's AP Managers, mostly ppl who are not Tech freindly

Industry/Entity Type

Software

Requirements
Must have
• i need on home page, the rotating banner should have 1 ability to place youtube links to show videos, and also ability to add buttons on these rotating banners that will allow forms to pop up take to another page.

```html
<!DOCTYPE html>
<html lang="en">
<head>
<meta charset="utf-8">
<title>KORVA – Intelligent Data Capture</title>
<link href="https://fonts.googleapis.com/css2?family=Ubuntu:ital,wght@0,300;0,400;0,500;1,400&display=swap" rel="stylesheet">
<style>
:root{
  --blue:#1a86c8;
  --blue-bright:#2aa0e6;
  --band-top:#3cb8f2;
  --band-bottom:#2a9ae0;
  --footer:#2b9be3;
  --text:#444;
  --muted:#8a8a8a;
  --light:#f4f4f4;
  --white:#fff;
}
*{margin:0;padding:0;box-sizing:border-box}
html,body{width:1097px;height:1200px;overflow:hidden;background:var(--white);font-family:"Ubuntu",sans-serif;color:var(--text)}
.page{position:relative;width:1097px;height:1200px}
.abs{position:absolute}
.header{left:0;top:0;width:1097px;height:144px;background:linear-gradient(#fff 0%,#f3f3f3 100%);border-bottom:1px solid #ddd}
.brand{left:135px;top:64px;display:flex;align-items:center;gap:6px}
.brand-name{font-size:31px;font-weight:500;color:var(--blue);letter-spacing:.5px}
.brand-mark{width:12px;height:12px;border-radius:50%;background:var(--blue)}
.nav a{position:absolute;top:83px;font-size:12.5px;color:#555;text-decoration:none}
.nav-pointer{left:456px;top:135px;width:0;height:0;border-left:8px solid transparent;border-right:8px solid transparent;border-bottom:9px solid var(--band-top)}
.band{left:0;top:144px;width:1097px;height:300px;background:linear-gradient(var(--band-top),var(--band-bottom))}
.hero{left:137px;top:171px;width:823px;height:280px;background:#fafafa}
.hero-photo{left:147px;top:179px;width:419px;height:251px;background:linear-gradient(100deg,#7a7c80 0%,#c9c8c2 40%,#eeede8 75%,#fafafa 100%)}
.hero-title{left:572px;top:206px;font-size:17px;font-weight:500;color:#666;letter-spacing:.3px}
.hero-arrows{left:883px;top:207px}
.hero-copy{left:572px;top:251px;width:347px;font-size:9.5px;line-height:15.5px;color:#666;text-align:justify}
.hero-copy p+p{margin-top:15px}
.btn{left:572px;top:368px;width:111px;height:31px;border-radius:3px;background:linear-gradient(#3fb2f0,#1e8fd8);border:1px solid #1b82c6;color:#fff;font-size:12.5px;line-height:29px;text-align:center}
.tagline{left:0;top:458px;width:1097px;text-align:center;font-size:12.5px;color:var(--blue)}
.tagline em{color:#888;margin-left:8px}
.divider{left:171px;top:494px;width:737px;height:6px;background:radial-gradient(ellipse at center,rgba(0,0,0,.35) 0%,rgba(0,0,0,0) 70%)}
.video{left:137px;top:536px;width:403px;height:250px;background:#fff;box-shadow:0 1px 4px rgba(0,0,0,.2)}
.video-screen{left:6px;top:6px;width:391px;height:238px;background:radial-gradient(circle at 50% 50%,#fafafa,#d6d6d6)}
.how-title{left:572px;top:541px;font-size:21px;font-weight:500;color:var(--blue)}
.how-copy{left:572px;top:582px;width:380px;font-size:10.5px;line-height:21px;color:#555}
.ticks{left:572px;top:648px;list-style:none}
.ticks li{position:relative;padding-left:32px;height:41.5px;font-size:12px;color:#444}
.ticks svg{position:absolute;left:0;top:2px}
.features{left:137px;top:857px;width:823px;height:171px;background:linear-gradient(#fafafa,#ececec);border:1px solid #ddd;box-shadow:0 2px 3px rgba(0,0,0,.2)}
.feature{position:absolute;top:0;width:260px;text-align:center}
.feature svg{position:absolute;left:116px;top:-18px}
.feature h3{margin-top:28px;font-size:13px;font-weight:400;color:#333}
.feature p{margin-top:14px;font-size:9.5px;line-height:17px;color:var(--muted)}
.feature a{display:block;margin-top:16px;font-size:12px;font-style:italic;color:var(--blue-bright);text-decoration:none}
.contact{top:1090px;display:flex;align-items:center;gap:12px;font-size:13px;color:#666}
.footer{left:0;top:1144px;width:1097px;height:56px;background:var(--footer);color:#e8f4fc;font-size:10.5px}
.footer span{position:absolute;top:22px}
.social{position:absolute;top:16px;width:23px;height:23px;border-radius:50%;background:#fff}
</style>
</head>
<body>
<div class="page">
  <header class="abs header">
    <div class="abs brand"><span class="brand-name">KORVA</span><span class="brand-mark"></span></div>
    <nav class="nav">
      <a style="left:349px">Home</a><a style="left:425px">Solutions</a><a style="left:518px">Products</a><a style="left:609px">Services</a><a style="left:697px">Resources</a><a style="left:794px">Support</a><a style="left:881px">Contact Us</a>
    </nav>
  </header>
  <div class="abs band"></div>
  <div class="abs nav-pointer"></div>

  <section class="abs hero">
  </section>
  <div class="abs hero-photo" role="img" aria-label="Businessman with laptop surrounded by sketched charts, formulas and a globe"></div>
  <h1 class="abs hero-title">ULTIMATE SCANNING SOFTWARE</h1>
  <svg class="abs hero-arrows" width="40" height="18" viewBox="0 0 40 18">
    <rect x="0.5" y="0.5" width="39" height="17" rx="8.5" fill="#eee" stroke="#bbb"/>
    <line x1="20" y1="2" x2="20" y2="16" stroke="#ccc"/>
    <path d="M13 5 L8 9 L13 13Z" fill="#2a9ae0"/><path d="M27 5 L32 9 L27 13Z" fill="#2a9ae0"/>
  </svg>
  <div class="abs hero-copy">
    <p>Lorem Ipsum is simply dummy text of the printing and typesetting industry. Lorem Ipsum has been the industry's standard dummy text ever since the 1500s.</p>
    <p>It was popularised in the 1960s with the release of Lettrine sheets containing Lorem Ipsum passages, and more recently with desktop publishing software like Folio Layout including versions of Lorem Ipsum.</p>
  </div>
  <div class="abs btn">Read More..</div>

  <div class="abs tagline">What the Intelligent Data Capture Software Will Do for the Business<em>Get a Quote</em></div>
  <div class="abs divider"></div>

  <div class="abs video">
    <div class="abs video-screen" role="img" aria-label="Dotted world map behind a video player"></div>
    <svg class="abs" style="left:180px;top:84px" width="42" height="76" viewBox="0 0 42 76"><path d="M0 0 L42 38 L0 76Z" fill="#2a9ae0"/></svg>
  </div>

  <h2 class="abs how-title">How it Works</h2>
  <p class="abs how-copy">Sed ut perspiciatis unde omnis iste natus error sit voluptatem accusantium doloremque rem aperiam."Easy to use small business software"</p>
  <ul class="abs ticks">
    <li><svg width="16" height="14"><path d="M1 7 L6 12 L15 1" fill="none" stroke="#3aa3e3" stroke-width="2"/></svg>Fusce scelerisque gravida nisl, in commodo mentum</li>
    <li><svg width="16" height="14"><path d="M1 7 L6 12 L15 1" fill="none" stroke="#3aa3e3" stroke-width="2"/></svg>Nam fermentum nisl vel nisl placerat porta.</li>
    <li><svg width="16" height="14"><path d="M1 7 L6 12 L15 1" fill="none" stroke="#3aa3e3" stroke-width="2"/></svg>In id lorem in ipsum suscipit facilisis.</li>
    <li><svg width="16" height="14"><path d="M1 7 L6 12 L15 1" fill="none" stroke="#3aa3e3" stroke-width="2"/></svg>Quisque et elit lorem, eget tincidunt mauris.</li>
  </ul>

  <section class="abs features">
    <div class="feature" style="left:3px">
      <svg width="28" height="28" viewBox="0 0 28 28"><g fill="none" stroke="#1a86c8" stroke-width="2"><circle cx="14" cy="14" r="12"/><ellipse cx="14" cy="14" rx="5" ry="12"/><line x1="2" y1="14" x2="26" y2="14"/><line x1="4" y1="8" x2="24" y2="8"/><line x1="4" y1="20" x2="24" y2="20"/></g></svg>
      <h3>Your business will run itself, day and night</h3>
      <p>"Sed ut perspiciatis unde omnis iste natus error si tore veritatis et quasi architecto beatae vitae dicta sunt explicabo</p>
      <a>Read More</a>
    </div>
    <div class="feature" style="left:278px">
      <svg width="28" height="36" viewBox="0 0 28 36"><path d="M15 2 h5 v16 h4 v14 h-18 v-14 h9z" fill="#1a86c8"/></svg>
      <h3 style="margin-top:25px">Refund requests made easy</h3>
      <p>"Sed ut perspiciatis unde omnis iste natus error si tore veritatis et quasi architecto beatae vitae dicta sunt explicabo</p>
      <a>Read More</a>
    </div>
    <div class="feature" style="left:562px">
      <svg width="28" height="28" viewBox="0 0 28 28"><g fill="none" stroke="#1a86c8" stroke-width="2"><path d="M6 24 A12 12 0 1 1 22 24"/><path d="M14 8 v12 M9 11 l10 6 M19 11 l-10 6"/></g></svg>
      <h3>Nam fermentum nisl vel nisl placerat</h3>
      <p>"Sed ut perspiciatis unde omnis iste natus error si tore veritatis et quasi architecto beatae vitae dicta sunt explicabo</p>
      <a>Read More</a>
    </div>
  </section>

  <div class="abs contact" style="left:137px">
    <svg width="29" height="29" viewBox="0 0 29 29"><circle cx="14.5" cy="14.5" r="13" fill="none" stroke="#888" stroke-width="2"/><path d="M10 8 l3 3 -2 2 q2 4 5 5 l2-2 3 3 -2 2 q-8 -1 -11 -11z" fill="#888"/></svg>
    <span>Call : (555)-214-7730</span>
  </div>
  <div class="abs contact" style="left:411px">
    <svg width="29" height="29" viewBox="0 0 29 29"><circle cx="14.5" cy="14.5" r="13" fill="none" stroke="#888" stroke-width="2"/><rect x="8" y="10" width="13" height="9" fill="#888"/><path d="M8 10 l6.5 5 6.5-5" fill="none" stroke="#fff"/></svg>
    <span>infocenter@korva.com</span>
  </div>
  <div class="abs contact" style="left:759px;gap:24px">
    <svg width="29" height="29" viewBox="0 0 29 29"><circle cx="14.5" cy="14.5" r="13" fill="none" stroke="#888" stroke-width="2"/><rect x="8" y="12" width="13" height="8" rx="1" fill="#888"/><rect x="10" y="8" width="9" height="4" fill="none" stroke="#888" stroke-width="1.5"/></svg>
    <span>(555) 410-2286</span>
  </div>

  <footer class="abs footer">
    <span style="left:136px">Copyright © 2012. All Rights Reserved</span>
    <span style="left:411px">Terms &amp; Condition &nbsp;&nbsp;|&nbsp;&nbsp; Privacy Policy</span>
    <span style="left:760px">Social Media</span>
    <i class="social" style="left:834px"></i><i class="social" style="left:865px"></i><i class="social" style="left:899px"></i><i class="social" style="left:935px"></i>
  </footer>
</div>
</body>
</html>
```